Corporate Business Card

Very professional, Modern, Not to busy, include phone address email, website
(253) 617-4930, 18761 52nd Avenue S, Kent, WA 98047, martin@plumlinegroup.com, varkoworks.com

Target Market(s)

Manufacturing

Industry/Entity Type

Aero, machining, manufacturing, Off road racing

Contact Information for Business Card

Phone, address email, website

```html
<!DOCTYPE html>
<html lang="en">
<head>
<meta charset="utf-8">
<title>Varko Works – Business Card</title>
<link rel="stylesheet" href="https://fonts.googleapis.com/css2?family=Lato:wght@400;700;900&family=Russo+One&display=swap">
<style>
  :root {
    --navy: #17356f;
    --red: #d42027;
    --white: #ffffff;
    --ink: #4a4a4a;
    --stage: #2a2a2c;
  }
  * { margin: 0; padding: 0; box-sizing: border-box; }
  html, body { width: 1200px; height: 718px; overflow: hidden; }
  body {
    background: var(--stage);
    font-family: "Lato", sans-serif;
    position: relative;
  }
  .card {
    position: absolute;
    top: 204px;
    width: 540px;
    height: 309px;
    overflow: hidden;
  }
  .card--front { left: 40px; background: var(--white); }
  .card--back { left: 620px; background: var(--navy); }

  .brand {
    position: absolute;
    font-family: "Lato", sans-serif;
    font-weight: 900;
    letter-spacing: 0.5px;
    white-space: nowrap;
  }
  .card--front .brand {
    top: 46px; right: 32px;
    font-size: 34px;
    color: var(--navy);
  }
  .card--back .brand {
    top: 50%; left: 50%;
    transform: translate(-50%, -50%);
    font-size: 58px;
    color: var(--white);
  }

  .person { position: absolute; left: 24px; top: 140px; }
  .person__name {
    font-family: "Russo One", sans-serif;
    font-size: 28px;
    font-weight: 400;
    color: var(--navy);
    letter-spacing: 0.5px;
    line-height: 1;
  }
  .person__title {
    margin-top: 5px;
    font-size: 14px;
    line-height: 1.2;
    color: var(--red);
  }
  .rule {
    position: absolute;
    left: 160px; right: 22px; top: 182px;
    height: 1.5px;
    background: var(--red);
  }
  .address {
    position: absolute;
    right: 30px; top: 192px;
    text-align: right;
    font-style: normal;
    font-size: 12.5px;
    line-height: 1.45;
    color: var(--ink);
  }
  .contact { position: absolute; left: 24px; top: 200px; list-style: none; }
  .contact__item {
    display: flex; align-items: center; gap: 8px;
    font-size: 12.5px; color: var(--ink);
    line-height: 20px;
  }
  .contact__icon { width: 11px; height: 11px; fill: var(--navy); }

  .band {
    position: absolute;
    left: 0; right: 0;
  }
  .band--red {
    top: 252px; height: 30px;
    background: var(--red);
    display: flex; align-items: center;
    padding-left: 24px;
  }
  .band--navy { top: 286px; height: 23px; background: var(--navy); }
  .website {
    font-size: 13px;
    letter-spacing: 2.5px;
    color: var(--white);
    text-transform: uppercase;
  }
</style>
</head>
<body>
  <section class="card card--front" aria-label="Business card front">
    <div class="brand">Varko Works</div>

    <div class="person">
      <h1 class="person__name">DALE PRESTON</h1>
      <p class="person__title">Managing Director</p>
    </div>
    <div class="rule"></div>

    <address class="address">
      18761 52nd Avenue S<br>
      Kent, WA 98047
    </address>

    <ul class="contact">
      <li class="contact__item">
        <svg class="contact__icon" viewBox="0 0 24 24" aria-hidden="true"><path d="M6.6 10.8a15.1 15.1 0 0 0 6.6 6.6l2.2-2.2a1 1 0 0 1 1-.25 11.4 11.4 0 0 0 3.6.57 1 1 0 0 1 1 1V20a1 1 0 0 1-1 1A17 17 0 0 1 3 4a1 1 0 0 1 1-1h3.5a1 1 0 0 1 1 1c0 1.25.2 2.45.57 3.57a1 1 0 0 1-.25 1z"/></svg>
        (253) 617-4930
      </li>
      <li class="contact__item">
        <svg class="contact__icon" viewBox="0 0 24 24" aria-hidden="true"><path d="M2 5h20v14H2z M2 5l10 8 10-8" stroke="var(--white)" stroke-width="1.5"/></svg>
        martin@plumlinegroup.com
      </li>
    </ul>

    <div class="band band--red"><p class="website">varkoworks.com</p></div>
    <div class="band band--navy"></div>
  </section>

  <section class="card card--back" aria-label="Business card back">
    <div class="brand">Varko Works</div>
  </section>
</body>
</html>
```